Very new and innovative Web design for Property managers of Vacation rentals

We are looking for a new website design for travel agencies and property managers specialised on vacation rentals business, holiday villas and apartments.

The end users of this website are travellers who are looking for a vacation home for their next holiday: this is the reason why the website must be easy to use, attractive, professional, possibly elegant and focused on get new reservations.

This is a draft of our current website: https://intro3.kelumsito.com/
Please consider that we would like to have proposals with a totally different and innovative layout, surprise us!

These are the pages of the website:
• Homepage: feel free to redesign all the homepage as you wish, surprise us with something very new! Please consider that Property manager/Travel agencies usually want to have the opportunity to put in evidence groups of houses with specific characteristics (eg. villas with private swimming pool, apartment in big/small towns, villas with air co, etc…), destinations and tourist areas, and sometimes experiences or activities (please consider that the website layout must be suitable even if some of the previous sections are not used).
• Search page: we’d like to organise the results of the search page in three different ways:
o Grid
o Map
o List
• Property page: to illustrate the characteristics, descriptions, images, …. of the property. It is very important to put in evidence images of the property and to maintain the booking form (and the other call to action bottom – eg. whatsapp) always visible
• Custom pages: static pages composed usually by text, images and call to actions
• Contact us (general form)
• Info request (specific of a property form)
• Booking process
• Blog, organised in four pages:
o Home Page – introduction to the blog
o List of articles
o Single article
o Site Map (presentation of categories and sub-categories)

If possible, we’d prefer to receive the material in Adobe XD or similar so that we can obtain the three versions:
- smartphone
- tablet
- desktop

The website will be then developed in Bootstrap: as a result we’ll need the icons in SVG format (or the library used)

In attachment you can find the map of the website pages

```html
<!DOCTYPE html>
<html lang="en">
<head>
<meta charset="utf-8">
<title>Villora – Blog page, desktop and mobile</title>
<link href="https://fonts.googleapis.com/css2?family=Playfair+Display:wght@400;700&family=Montserrat:wght@400;500;600;700&display=swap" rel="stylesheet">
<style>
:root{
  --bg-top:#0b5a45;
  --bg-top-dark:#06362a;
  --bg-bottom:#5e7b70;
  --brand:#14b88a;
  --ink:#222;
  --muted:#8a8a8a;
  --line:#e6e6e6;
  --footer:#1c1c1c;
  --footer-text:#bdbdbd;
  --white:#fff;
  --cat-bar:#eef1f6;
}
*{margin:0;padding:0;box-sizing:border-box}
html,body{width:702px;height:1200px;overflow:hidden}
body{position:relative;background:var(--bg-bottom);font-family:"Montserrat",sans-serif;color:var(--ink)}
.stage-top{position:absolute;left:0;top:0;width:702px;height:341px;background:radial-gradient(ellipse at 60% 10%,var(--bg-top) 0%,var(--bg-top-dark) 100%)}
.brand-mark{position:absolute;left:81px;top:31px;display:flex;align-items:center;gap:8px}
.brand-mark .dot{width:24px;height:24px;border-radius:50%;background:var(--brand)}
.brand-mark .name{font-family:"Montserrat",sans-serif;font-weight:500;font-size:26px;color:var(--white);letter-spacing:.3px}
.label-vertical{position:absolute;font-family:"Playfair Display",serif;color:var(--white);font-size:46px;white-space:nowrap;line-height:1}
.label-desktop{left:16px;top:890px;transform:rotate(-90deg);transform-origin:0 0}
.label-mobile{left:632px;top:305px;transform:rotate(90deg);transform-origin:0 0}

.logo{display:flex;align-items:center;gap:2px;font-weight:500;color:var(--ink)}
.logo .dot{border-radius:50%;background:var(--brand)}
.thumb{position:absolute;left:0;top:0;width:100%}
.meta{position:absolute;left:0;font-size:2.4px;color:var(--ink);white-space:nowrap}
.title{position:absolute;left:0;font-family:"Playfair Display",serif;font-weight:400;color:var(--ink);line-height:1.2}
.excerpt{position:absolute;left:0;font-size:2.3px;line-height:1.5;color:var(--muted)}
.btn{position:absolute;left:0;background:var(--brand);color:var(--white);font-weight:700;display:flex;align-items:center;justify-content:center;letter-spacing:.1px}
.img-desk{background:linear-gradient(135deg,#8a3a2c,#d9b07a 60%,#f1e2c6)}
.img-dinner{background:linear-gradient(135deg,#e8b06a,#f5e6d0 55%,#c98d55)}
.img-pool{background:linear-gradient(180deg,#a56c3f,#e3a45f 40%,#3ba6b8 70%,#e07c4b)}
.img-basilica{background:linear-gradient(180deg,#0e1e3f,#24417a 45%,#c98f3f 70%,#3a2a14)}
.img-canal{background:linear-gradient(135deg,#b8c6d6,#6c5a44 50%,#24403f)}
.img-bed{background:linear-gradient(135deg,#4f5860,#c9b7a3 55%,#8e7a66)}
.hero{background:linear-gradient(90deg,#6a6253 0%,#4a4d4a 40%,#25384a 70%,#2a4158 100%)}

.desktop{position:absolute;left:72px;top:404px;width:278px;height:573px;background:var(--white);overflow:hidden}
.desktop .topbar{position:absolute;right:0;top:0;width:91px;height:9px;background:var(--brand);clip-path:polygon(0 0,100% 0,100% 100%,8px 100%);display:flex;align-items:center;justify-content:flex-end;gap:6px;padding-right:8px;font-size:2.4px;font-weight:700;color:var(--white)}
.desktop .logo{position:absolute;left:25px;top:6px;font-size:6.6px}
.desktop .logo .dot{width:6px;height:6px}
.desktop .nav{position:absolute;left:0;top:14px;width:100%;font-size:2.8px;color:#444}
.desktop .nav span{position:absolute;white-space:nowrap}
.desktop .nav-rule{position:absolute;left:116px;right:0;top:21px;height:.5px;background:var(--line)}
.desktop .hero{position:absolute;left:0;top:21px;width:100%;height:66px}
.hero-title{position:absolute;font-family:"Playfair Display",serif;font-weight:700;color:var(--white)}
.desktop .hero-title{left:0;width:100%;top:48px;text-align:center;font-size:11px}
.desktop .crumb{position:absolute;left:26px;top:95px;font-size:2.4px;color:var(--muted)}
.desktop .crumb b{color:var(--ink);font-weight:600}
.d-card{position:absolute;width:71px;height:118px}
.d-card .thumb{height:52px}
.d-card .meta{top:60px}
.d-card .title{top:67px;font-size:6px}
.d-card .excerpt{top:86px;width:71px}
.d-card .btn{top:109px;width:27px;height:10px;font-size:2.6px}
.categories{position:absolute;left:193px;top:110px;width:58px;height:111px;border:.5px solid var(--line);padding:6px 6px 0}
.categories h3{font-family:"Playfair Display",serif;font-weight:400;font-size:4.4px;letter-spacing:.2px;margin-bottom:3.5px}
.categories li{list-style:none;display:flex;justify-content:space-between;font-size:2.5px;height:9.55px;align-items:center;color:#444}
.desktop .footer{position:absolute;left:0;top:497px;width:100%;height:76px;background:var(--footer);color:var(--footer-text)}
.desktop .footer .logo{left:25px;top:29px;font-size:5.4px;color:var(--white)}
.desktop .footer .logo .dot{width:5px;height:5px}
.f-col{position:absolute;top:15px}
.f-col h4{font-family:"Playfair Display",serif;font-weight:400;font-size:3.8px;color:var(--white);margin-bottom:4px}
.f-col li{list-style:none;font-size:2.4px;height:6.4px;display:flex;align-items:flex-start;gap:2px}
.f-col svg{flex:none}
.desktop .copyright{position:absolute;top:60px;width:100%;text-align:center;font-size:2.3px}

.mobile{position:absolute;left:484px;top:174px;width:90px;height:966px;background:var(--white);overflow:hidden}
.mobile .logo{position:absolute;left:0;width:100%;justify-content:center;top:3px;font-size:6px}
.mobile .logo .dot{width:5.5px;height:5.5px}
.mobile .greenbar{position:absolute;left:0;top:16px;width:100%;height:11px;background:var(--brand);display:flex;align-items:center;justify-content:space-between;padding:0 3px}
.burger{width:8px;height:5px;display:flex;flex-direction:column;justify-content:space-between}
.burger i{display:block;height:.7px;background:var(--white)}
.mobile .greenbar .tools{display:flex;gap:2px;align-items:center;font-size:3px;font-weight:700;color:var(--white)}
.mobile .hero{position:absolute;left:0;top:27px;width:100%;height:22px}
.mobile .hero-title{left:0;width:100%;top:8px;text-align:center;font-size:4px}
.mobile .crumb{position:absolute;left:0;width:100%;top:52px;text-align:center;font-size:3.4px;color:var(--muted)}
.mobile .crumb b{color:var(--ink);font-weight:500}
.m-post{position:absolute;left:2px;width:86px;height:122px}
.m-post .thumb{height:63px}
.m-post .meta{top:69px;font-size:2.6px}
.m-post .title{top:77px;font-size:4.8px;white-space:nowrap}
.m-post .excerpt{top:87px;width:86px;font-size:2.55px}
.m-post .btn{top:108px;width:32px;height:10.5px;font-size:3px}
.m-cats{position:absolute;left:2px;top:693px;width:86px;height:13px;background:var(--cat-bar);display:flex;align-items:center;justify-content:space-between;padding:0 4px;font-family:"Playfair Display",serif;font-size:4.6px}
.mobile .footer{position:absolute;left:0;top:716px;width:100%;height:250px;background:var(--footer);color:var(--footer-text);padding:0 2px}
.m-group{position:absolute;left:2px;width:86px}
.m-group h4{font-family:"Playfair Display",serif;font-weight:400;font-size:5.4px;color:var(--white);margin-bottom:3.5px}
.m-group li{list-style:none;font-size:3.7px;height:9px;display:flex;align-items:flex-start;gap:2.5px}
.m-group .social li{height:11px;align-items:center}
.sicon{width:8.5px;height:8.5px;border-radius:50%;background:var(--white);flex:none}
.dsicon{width:5px;height:5px;border-radius:50%;background:var(--white);flex:none}
.mobile .footer .logo{top:232px;font-size:5.4px;color:var(--white)}
.mobile .footer .logo .dot{width:5px;height:5px}
.mobile .copyright{position:absolute;left:0;top:243px;width:100%;text-align:center;font-size:2.8px}
</style>
</head>
<body>

<div class="stage-top"></div>
<div class="brand-mark"><span class="dot"></span><span class="name">Villora</span></div>

<div class="label-vertical label-desktop">Desktop Version</div>
<div class="label-vertical label-mobile">Mobile Version</div>

<section class="desktop">
  <div class="topbar"><span>LOGIN</span><span>WHISHLIST</span><span>EN ˅</span></div>
  <div class="logo"><span class="dot"></span>Villora</div>
  <nav class="nav">
    <span style="left:132px">HOME</span>
    <span style="left:153px">SEARCH</span>
    <span style="left:178px">PROPERTY</span>
    <span style="left:206px">CUSTOM</span>
    <span style="left:232px">CONTACT US</span>
  </nav>
  <div class="nav-rule"></div>
  <div class="hero" role="img" aria-label="Coastal hilltop town with an old stone church above the sea and a passing yacht"></div>
  <div class="hero-title">BLOG</div>
  <div class="crumb">Home / <b>Blog</b></div>

  <article class="d-card" style="left:26px;top:110px">
    <div class="thumb img-desk" role="img" aria-label="Hotel receptionist welcoming a guest at the front desk"></div>
    <div class="meta">Mara Lenti &nbsp;|&nbsp; December 4, 2020 &nbsp;|&nbsp; 0 Comments</div>
    <h2 class="title">One who avoids a pain that resultant</h2>
    <p class="excerpt">Nam libero tempore, cum soluta nobis est eligendi optio cumque nihil impedit quo minus id quod maxime placeat facere possimus, omnis voluptas assumenda est, omnis dolor repellendus.</p>
    <div class="btn">READ MORE</div>
  </article>
  <article class="d-card" style="left:103px;top:110px">
    <div class="thumb img-dinner" role="img" aria-label="Restaurant table set with plates and glasses"></div>
    <div class="meta">Mara Lenti &nbsp;|&nbsp; December 4, 2020 &nbsp;|&nbsp; 0 Comments</div>
    <h2 class="title">One who avoids a pain that resultant</h2>
    <p class="excerpt">Nam libero tempore, cum soluta nobis est eligendi optio cumque nihil impedit quo minus id quod maxime placeat facere possimus, omnis voluptas assumenda est, omnis dolor repellendus.</p>
    <div class="btn">READ MORE</div>
  </article>
  <article class="d-card" style="left:26px;top:236px">
    <div class="thumb img-pool" role="img" aria-label="Guest relaxing in a hotel swimming pool"></div>
    <div class="meta">Mara Lenti &nbsp;|&nbsp; December 4, 2020 &nbsp;|&nbsp; 0 Comments</div>
    <h2 class="title">One who avoids a pain that resultant</h2>
    <p class="excerpt">Nam libero tempore, cum soluta nobis est eligendi optio cumque nihil impedit quo minus id quod maxime placeat facere possimus, omnis voluptas assumenda est, omnis dolor repellendus.</p>
    <div class="btn">READ MORE</div>
  </article>
  <article class="d-card" style="left:103px;top:236px">
    <div class="thumb img-basilica" role="img" aria-label="Domed basilica and square lit at night"></div>
    <div class="meta">Mara Lenti &nbsp;|&nbsp; December 4, 2020 &nbsp;|&nbsp; 0 Comments</div>
    <h2 class="title">One who avoids a pain that resultant</h2>
    <p class="excerpt">Nam libero tempore, cum soluta nobis est eligendi optio cumque nihil impedit quo minus id quod maxime placeat facere possimus, omnis voluptas assumenda est, omnis dolor repellendus.</p>
    <div class="btn">READ MORE</div>
  </article>
  <article class="d-card" style="left:26px;top:363px">
    <div class="thumb img-canal" role="img" aria-label="Shopping arcade along an indoor canal"></div>
    <div class="meta">Mara Lenti &nbsp;|&nbsp; December 4, 2020 &nbsp;|&nbsp; 0 Comments</div>
    <h2 class="title">One who avoids a pain that resultant</h2>
    <p class="excerpt">Nam libero tempore, cum soluta nobis est eligendi optio cumque nihil impedit quo minus id quod maxime placeat facere possimus, omnis voluptas assumenda est, omnis dolor repellendus.</p>
    <div class="btn">READ MORE</div>
  </article>
  <article class="d-card" style="left:103px;top:363px">
    <div class="thumb img-bed" role="img" aria-label="Bedroom with white sheets by a large window"></div>
    <div class="meta">Mara Lenti &nbsp;|&nbsp; December 4, 2020 &nbsp;|&nbsp; 0 Comments</div>
    <h2 class="title">One who avoids a pain that resultant</h2>
    <p class="excerpt">Nam libero tempore, cum soluta nobis est eligendi optio cumque nihil impedit quo minus id quod maxime placeat facere possimus, omnis voluptas assumenda est, omnis dolor repellendus.</p>
    <div class="btn">READ MORE</div>
  </article>

  <aside class="categories">
    <h3>CATEGORIES</h3>
    <ul>
      <li><span>Consectetur Adipiscing</span><span>+</span></li>
      <li><span>Eget Tempor</span><span>+</span></li>
      <li><span>Lobortis Dictum</span><span>+</span></li>
      <li><span>Tempus Fermentum</span><span>+</span></li>
      <li><span>Quisque</span><span>+</span></li>
      <li><span>Consectetur Adipiscing</span><span>+</span></li>
      <li><span>Eget Tempor</span><span>+</span></li>
      <li><span>Lobortis Dictum</span><span>+</span></li>
      <li><span>Tempus Fermentum</span><span>+</span></li>
      <li><span>Quisque</span><span>+</span></li>
    </ul>
  </aside>

  <footer class="footer">
    <div class="logo"><span class="dot"></span>Villora</div>
    <div class="f-col" style="left:77px">
      <h4>Quick Links</h4>
      <ul><li>Home</li><li>Search</li><li>Property</li><li>Custom</li><li>Contact Us</li></ul>
    </div>
    <div class="f-col" style="left:121px">
      <h4>Company</h4>
      <ul><li>Privacy Policies</li><li>Reservation Policies</li><li>Cookie Policy</li></ul>
    </div>
    <div class="f-col" style="left:168px">
      <h4>Contact Us</h4>
      <ul>
        <li style="height:10px"><svg width="2.6" height="3.2" viewBox="0 0 10 13"><path d="M5 0a5 5 0 0 0-5 5c0 4 5 8 5 8s5-4 5-8a5 5 0 0 0-5-5zm0 7a2 2 0 1 1 0-4 2 2 0 0 1 0 4z" fill="#fff"/></svg><span>Via dei Tigli 7, 52100<br>Borgoverde (Italy)</span></li>
        <li><svg width="2.6" height="2.6" viewBox="0 0 10 10"><path d="M2 0l2 2.5-1.2 1.3a6 6 0 0 0 3.4 3.4L7.5 6 10 8l-1.5 2C4 10 0 6 0 1.5z" fill="#fff"/></svg><span>+39 055 4172830</span></li>
        <li><svg width="2.8" height="2.2" viewBox="0 0 12 9"><rect width="12" height="9" fill="#fff"/><path d="M0 0l6 5 6-5" stroke="#1c1c1c" fill="none"/></svg><span>hello@villora.com</span></li>
      </ul>
    </div>
    <div class="f-col" style="left:229px">
      <h4>Follow Us</h4>
      <ul><li style="height:8px;align-items:center"><span class="dsicon"></span>Sharely</li><li style="height:8px;align-items:center"><span class="dsicon"></span>Buzzline</li><li style="height:8px;align-items:center"><span class="dsicon"></span>Photonest</li></ul>
    </div>
    <div class="copyright">Copyright © 2021 <b style="color:#fff">Villora</b>. All rights reserved.</div>
  </footer>
</section>

<section class="mobile">
  <div class="logo"><span class="dot"></span>Villora</div>
  <div class="greenbar">
    <div class="burger"><i></i><i></i><i></i></div>
    <div class="tools">
      <svg width="4" height="4" viewBox="0 0 10 10"><circle cx="5" cy="3" r="2.3" fill="none" stroke="#fff"/><path d="M1 10c0-3 2-4.5 4-4.5S9 7 9 10" fill="none" stroke="#fff"/></svg>
      <svg width="4.4" height="4" viewBox="0 0 11 10"><path d="M5.5 9.5L1 5a2.6 2.6 0 0 1 4.5-3 2.6 2.6 0 0 1 4.5 3z" fill="none" stroke="#fff"/></svg>
      <span>EN ˅</span>
    </div>
  </div>
  <div class="hero" role="img" aria-label="Coastal hilltop town with an old stone church above the sea"></div>
  <div class="hero-title">BLOG</div>
  <div class="crumb">Home &nbsp;/&nbsp; <b>Blog</b></div>

  <article class="m-post" style="top:63px">
    <div class="thumb img-desk" role="img" aria-label="Hotel receptionist welcoming a guest at the front desk"></div>
    <div class="meta">Mara Lenti &nbsp;|&nbsp; December 4, 2020 &nbsp;|&nbsp; 0 Comments</div>
    <h2 class="title">One who avoids a pain that resultant</h2>
    <p class="excerpt">Nam libero tempore, cum soluta nobis est eligendi optio cumque nihil impedit quo minus id quod maxime placeat facere possimus, omnis voluptas assumenda est, omnis dolor repellendus.</p>
    <div class="btn">READ MORE</div>
  </article>
  <article class="m-post" style="top:190px">
    <div class="thumb img-pool" role="img" aria-label="Guest relaxing in a hotel swimming pool"></div>
    <div class="meta">Mara Lenti &nbsp;|&nbsp; December 4, 2020 &nbsp;|&nbsp; 0 Comments</div>
    <h2 class="title">One who avoids a pain that resultant</h2>
    <p class="excerpt">Nam libero tempore, cum soluta nobis est eligendi optio cumque nihil impedit quo minus id quod maxime placeat facere possimus, omnis voluptas assumenda est, omnis dolor repellendus.</p>
    <div class="btn">READ MORE</div>
  </article>
  <article class="m-post" style="top:318px">
    <div class="thumb img-basilica" role="img" aria-label="Domed basilica and square lit at night"></div>
    <div class="meta">Mara Lenti &nbsp;|&nbsp; December 4, 2020 &nbsp;|&nbsp; 0 Comments</div>
    <h2 class="title">One who avoids a pain that resultant</h2>
    <p class="excerpt">Nam libero tempore, cum soluta nobis est eligendi optio cumque nihil impedit quo minus id quod maxime placeat facere possimus, omnis voluptas assumenda est, omnis dolor repellendus.</p>
    <div class="btn">READ MORE</div>
  </article>
  <article class="m-post" style="top:442px">
    <div class="thumb img-canal" role="img" aria-label="Shopping arcade along an indoor canal"></div>
    <div class="meta">Mara Lenti &nbsp;|&nbsp; December 4, 2020 &nbsp;|&nbsp; 0 Comments</div>
    <h2 class="title">One who avoids a pain that resultant</h2>
    <p class="excerpt">Nam libero tempore, cum soluta nobis est eligendi optio cumque nihil impedit quo minus id quod maxime placeat facere possimus, omnis voluptas assumenda est, omnis dolor repellendus.</p>
    <div class="btn">READ MORE</div>
  </article>
  <article class="m-post" style="top:568px">
    <div class="thumb img-bed" role="img" aria-label="Bedroom with white sheets by a large window"></div>
    <div class="meta">Mara Lenti &nbsp;|&nbsp; December 4, 2020 &nbsp;|&nbsp; 0 Comments</div>
    <h2 class="title">One who avoids a pain that resultant</h2>
    <p class="excerpt">Nam libero tempore, cum soluta nobis est eligendi optio cumque nihil impedit quo minus id quod maxime placeat facere possimus, omnis voluptas assumenda est, omnis dolor repellendus.</p>
    <div class="btn">READ MORE</div>
  </article>

  <div class="m-cats"><span>CATEGORIES</span><span style="font-family:Montserrat,sans-serif">›</span></div>

  <footer class="footer">
    <div class="m-group" style="top:8px">
      <h4>Quick Links</h4>
      <ul><li>Home</li><li>Search</li><li>Property</li><li>Custom</li><li>Contact Us</li></ul>
    </div>
    <div class="m-group" style="top:70px">
      <h4>Company</h4>
      <ul><li>Privacy Policies</li><li>Reservation Policies</li><li>Cookie Policy</li></ul>
    </div>
    <div class="m-group" style="top:113px">
      <h4>Contact Us</h4>
      <ul>
        <li style="height:16px"><svg width="4" height="5" viewBox="0 0 10 13"><path d="M5 0a5 5 0 0 0-5 5c0 4 5 8 5 8s5-4 5-8a5 5 0 0 0-5-5zm0 7a2 2 0 1 1 0-4 2 2 0 0 1 0 4z" fill="#fff"/></svg><span>Via dei Tigli 7, 52100<br>Borgoverde (Italy)</span></li>
        <li style="height:12px"><svg width="4" height="4" viewBox="0 0 10 10"><path d="M2 0l2 2.5-1.2 1.3a6 6 0 0 0 3.4 3.4L7.5 6 10 8l-1.5 2C4 10 0 6 0 1.5z" fill="#fff"/></svg><span>+39 055 4172830</span></li>
        <li><svg width="4.4" height="3.4" viewBox="0 0 12 9"><rect width="12" height="9" fill="#fff"/><path d="M0 0l6 5 6-5" stroke="#1c1c1c" fill="none"/></svg><span>hello@villora.com</span></li>
      </ul>
    </div>
    <div class="m-group" style="top:170px">
      <h4>Follow Us</h4>
      <ul class="social"><li><span class="sicon"></span>Sharely</li><li><span class="sicon"></span>Buzzline</li><li><span class="sicon"></span>Photonest</li></ul>
    </div>
    <div class="logo"><span class="dot"></span>Villora</div>
    <div class="copyright">Copyright © 2021 <b style="color:#fff">Villora</b>. All rights reserved.</div>
  </footer>
</section>

</body>
</html>
```